Local Flower Farm Needs Business Card Design

I need business cards designed for a flower farm based in Eudora, Kansas.
Business Info:
We are a local cut flower farm located in Eudora, Kansas, founded by Corinne Haldwick. What started as a passion for agriculture and search for more joy in daily life has blossomed into a small business dedicated to providing the community with beautiful, fresh, and sustainable flowers. We specialize in local, seasonal blooms, ensuring that every petal reflects the care and dedication we pour into our craft. Our mission is to deliver the highest quality flowers directly to our customers through local farmers markets and to florists who share our commitment to sustainability. Join us in celebrating the beauty of nature, one bloom at a time!
Contact Details:
Corinne Haldwick
Owner
Phone 913-555-0147
Facebook: Rosalind Thorpe Gardens
Instagram: @RosalindThorpeGardens
Website: RosalindThorpeGardens.example
Target Market(s)
Wholesale to Florists and Direct to Consumer via Farmers Market
Industry/Entity Type
Florist, Farm
Contact Information for Business Card
Name, Contact Info, Logo
Look and feel
Each slider illustrates characteristics of the customer's brand and the style your logo design should communicate.

```html
<!DOCTYPE html>
<html lang="en">
<head>
<meta charset="utf-8">
<title>Rosalind Thorpe Gardens – Business Card</title>
<link href="https://fonts.googleapis.com/css2?family=Tinos:wght@400;700&display=swap" rel="stylesheet">
<style>
  :root {
    --ink: #0b2730;
    --paper: #ffffff;
    --backdrop: #e1e5e7;
  }
  * { margin: 0; padding: 0; box-sizing: border-box; }
  html, body { width: 1200px; height: 960px; overflow: hidden; }
  body {
    background: var(--backdrop);
    font-family: "Tinos", "Times New Roman", serif;
    position: relative;
  }
  .card {
    position: absolute;
    left: 246px;
    width: 708px;
    height: 404px;
    overflow: hidden;
  }
  .card--front { top: 58px; background: var(--ink); }
  .card--back { top: 500px; background: var(--paper); }

  .brand-seal {
    position: absolute;
    border-radius: 50%;
    display: flex;
    align-items: center;
    justify-content: center;
    text-align: center;
    line-height: 1.25;
    letter-spacing: 0.06em;
    text-transform: uppercase;
  }
  .card--front .brand-seal {
    width: 270px; height: 270px;
    left: 219px; top: 67px;
    border: 1px solid var(--paper);
    color: var(--paper);
    font-size: 26px;
  }
  .card--back .brand-seal {
    width: 174px; height: 174px;
    left: 26px; top: 24px;
    border: 1px solid var(--ink);
    color: var(--ink);
    font-size: 17px;
  }

  .holder {
    position: absolute;
    right: 30px;
    top: 28px;
    text-align: right;
    color: #000;
  }
  .holder__name { font-weight: 700; font-size: 33px; letter-spacing: 0.02em; line-height: 1; }
  .holder__role { font-size: 18px; margin-top: 2px; }
  .edge-tab {
    position: absolute;
    right: 0; top: 32px;
    width: 19px; height: 53px;
    background: var(--ink);
  }

  .contact-band {
    position: absolute;
    left: 0; right: 0; bottom: 0;
    height: 134px;
    background: var(--ink);
  }
  .contact-list {
    list-style: none;
    position: absolute;
    left: 25px; top: 14px;
    color: var(--paper);
    font-size: 17px;
    letter-spacing: 0.02em;
  }
  .contact-list li {
    display: flex;
    align-items: center;
    height: 24px;
    white-space: nowrap;
  }
  .contact-list svg { width: 17px; height: 17px; margin-right: 9px; flex: none; }
  .bullet-dot {
    width: 17px; height: 17px; margin-right: 9px;
    border-radius: 50%; background: var(--paper); flex: none;
  }
  .bullet-square {
    width: 16px; height: 16px; margin-right: 10px;
    border: 2px solid var(--paper); border-radius: 4px; flex: none;
  }
  .band-mark {
    position: absolute;
    right: 0; top: 0;
    width: 150px; height: 134px;
    background: var(--paper);
    color: var(--ink);
    display: flex;
    align-items: center;
    justify-content: center;
    text-align: center;
    font-size: 15px;
    line-height: 1.3;
    text-transform: uppercase;
    letter-spacing: 0.06em;
  }
</style>
</head>
<body>

  <section class="card card--front" aria-label="Card front">
    <div class="brand-seal">Rosalind<br>Thorpe<br>Gardens</div>
  </section>

  <section class="card card--back" aria-label="Card back">
    <div class="brand-seal">Rosalind<br>Thorpe<br>Gardens</div>

    <div class="holder">
      <p class="holder__name">Corinne Haldwick</p>
      <p class="holder__role">Owner</p>
    </div>
    <div class="edge-tab"></div>

    <div class="contact-band">
      <ul class="contact-list">
        <li>
          <svg viewBox="0 0 24 24" aria-hidden="true"><path fill="#fff" d="M6.6 10.8a15.1 15.1 0 0 0 6.6 6.6l2.2-2.2c.3-.3.7-.4 1-.2 1.1.4 2.3.6 3.6.6.6 0 1 .4 1 1V20c0 .6-.4 1-1 1A17 17 0 0 1 3 4c0-.6.4-1 1-1h3.5c.6 0 1 .4 1 1 0 1.3.2 2.5.6 3.6.1.3 0 .7-.2 1z"/></svg>
          913-555-0147
        </li>
        <li><span class="bullet-dot"></span>Rosalind Thorpe Gardens</li>
        <li><span class="bullet-square"></span>@RosalindThorpeGardens</li>
        <li>
          <svg viewBox="0 0 24 24" aria-hidden="true"><circle cx="12" cy="12" r="10" fill="none" stroke="#fff" stroke-width="2"/><path d="M2 12h20M12 2c3 3 3 17 0 20M12 2c-3 3-3 17 0 20" fill="none" stroke="#fff" stroke-width="1.6"/></svg>
          RosalindThorpeGardens.example
        </li>
      </ul>
      <div class="band-mark">Rosalind<br>Thorpe<br>Gardens</div>
    </div>
  </section>

</body>
</html>
```